RTavenor Business Cards & Letterhead

I have a logo but need a design for some new business cards. We are a Design-Build Firm that specializes in the design and construction of commercial projects.
the cards need to be professional. no cartoon stuff.
i would like to have the cards in AI format so I can update the card as needed. Logo is provided.
Our Address is: 4187 Marlowe Ct. Larkmoor, Eastvale 27614

```html
<!DOCTYPE html>
<html lang="en">
<head>
<meta charset="utf-8">
<title>RTavenor Business Card</title>
<link href="https://fonts.googleapis.com/css2?family=Montserrat:wght@400;500;700;800&display=swap" rel="stylesheet">
<style>
  :root {
    --backdrop: #121212;
    --card: #2a2a2a;
    --ink: #ffffff;
    --ink-soft: #e6e6e6;
    --accent: #2b86c5;
  }
  * { box-sizing: border-box; margin: 0; padding: 0; }
  html, body {
    width: 1200px;
    height: 900px;
    overflow: hidden;
    background: var(--backdrop);
    font-family: "Montserrat", Arial, sans-serif;
  }
  .canvas {
    width: 1200px;
    height: 900px;
    display: flex;
    flex-direction: column;
    align-items: center;
    justify-content: center;
    gap: 40px;
  }
  .card {
    width: 700px;
    height: 400px;
    background: linear-gradient(135deg, #222222 0%, var(--card) 55%, #3a3a3a 100%);
    position: relative;
    box-shadow: 0 10px 24px rgba(0,0,0,0.55);
  }
  .wordmark {
    display: flex;
    align-items: center;
    gap: 14px;
    color: var(--ink);
    font-weight: 800;
    letter-spacing: 0.02em;
    white-space: nowrap;
  }
  .wordmark-square {
    background: var(--accent);
    flex: none;
  }
  .card-front {
    display: flex;
    align-items: center;
    justify-content: center;
  }
  .card-front .wordmark { font-size: 64px; }
  .card-front .wordmark-square { width: 44px; height: 44px; }

  .card-back .wordmark {
    position: absolute;
    left: 48px;
    top: 172px;
    font-size: 34px;
    gap: 10px;
  }
  .card-back .wordmark-square { width: 24px; height: 24px; }
  .divider {
    position: absolute;
    left: 352px;
    top: 92px;
    width: 2px;
    height: 220px;
    background: var(--accent);
  }
  .details {
    position: absolute;
    left: 384px;
    top: 94px;
    width: 300px;
    color: var(--ink-soft);
  }
  .person-name {
    color: var(--accent);
    font-weight: 700;
    font-size: 28px;
    letter-spacing: 0.06em;
    text-transform: uppercase;
    line-height: 1;
    white-space: nowrap;
  }
  .person-title {
    font-size: 15px;
    font-weight: 500;
    letter-spacing: 0.08em;
    margin-top: 4px;
  }
  .address {
    font-style: normal;
    font-size: 15px;
    line-height: 1.45;
    letter-spacing: 0.03em;
    margin-top: 18px;
    white-space: nowrap;
  }
  .contact-list {
    list-style: none;
    margin-top: 16px;
    font-size: 15px;
    letter-spacing: 0.03em;
  }
  .contact-list li {
    display: flex;
    align-items: center;
    gap: 10px;
    line-height: 1.7;
    white-space: nowrap;
  }
  .contact-icon { width: 14px; height: 14px; flex: none; }
  .icon-fill { fill: var(--accent); }
  .icon-line { fill: none; stroke: var(--accent); }
  .icon-cut { fill: none; stroke: var(--card); stroke-width: 1.8; }
</style>
</head>
<body>
<main class="canvas">
  <section class="card card-front">
    <div class="wordmark"><span class="wordmark-square"></span>RTAVENOR</div>
  </section>

  <section class="card card-back">
    <div class="wordmark"><span class="wordmark-square"></span>RTAVENOR</div>
    <div class="divider"></div>
    <div class="details">
      <h1 class="person-name">Jonah Pell</h1>
      <p class="person-title">MANAGER</p>
      <address class="address">4187 Marlowe Ct.<br>Larkmoor, Eastvale 27614</address>
      <ul class="contact-list">
        <li>
          <svg class="contact-icon" viewBox="0 0 24 24"><path class="icon-fill" d="M6.6 10.8a15.1 15.1 0 0 0 6.6 6.6l2.2-2.2a1 1 0 0 1 1-.25 11.4 11.4 0 0 0 3.6.57 1 1 0 0 1 1 1V20a1 1 0 0 1-1 1A17 17 0 0 1 3 4a1 1 0 0 1 1-1h3.5a1 1 0 0 1 1 1c0 1.25.2 2.45.57 3.57a1 1 0 0 1-.25 1z"/></svg>
          123-456-7890
        </li>
        <li>
          <svg class="contact-icon" viewBox="0 0 24 24"><rect class="icon-fill" x="2" y="5" width="20" height="14" rx="1"/><path class="icon-cut" d="M3 6l9 7 9-7"/></svg>
          info@youremail.com
        </li>
        <li>
          <svg class="contact-icon" viewBox="0 0 24 24"><circle class="icon-line" cx="12" cy="12" r="9" stroke-width="2"/><ellipse class="icon-line" cx="12" cy="12" rx="4" ry="9" stroke-width="1.6"/><path class="icon-line" d="M3 12h18M5 7.5h14M5 16.5h14" stroke-width="1.4"/></svg>
          www.yourwebsite.com
        </li>
      </ul>
    </div>
  </section>
</main>
</body>
</html>
```